New Business Card for Web Design/Internet Marketing Company

Looking for a great looking new business card. We are a 10 year old web design, internet marketing and website management company that works mostly with small businesses.

Our new card needs to better match the colors and style of our website, be bold, extremely usable and slightly edgy.

Target Market(s)

Small/Medium businesses that have websites

Industry/Entity Type

Internet

Requirements
Must have
• Front and back design, full color, rounded corners please

Must use the colors/style of our website (JPG provided)

INFO FOR CARDS (as readable as possible please)
Mark Lenner
President/CEO
mark@trelvanmedia.example
Phone: 520-381-7459
Toll Free: 866-381-7459
Address: 4315 W. Calloway Ave. Ste. 140, Tucson, AZ 85792

THINGS I WANT TO PROMOTE (if there is room):
1. Our Website - www.trelvanmedia.example

2. Social Media
Twitter: @trelvanmedia
Facebook: www.facebook.com/trelvanmedia

3. Our Services
Web Design
Internet Marketing
Website Management

```html
<!DOCTYPE html>
<html lang="en">
<head>
<meta charset="utf-8">
<title>Trelvan Media – Business Card</title>
<link rel="stylesheet" href="https://fonts.googleapis.com/css2?family=Source+Sans+3:wght@300;400;600;700&display=swap">
<style>
  :root {
    --backdrop: #1d1d1e;
    --navy: #234c92;
    --blue-light: #4a8fc2;
    --blue-text: #1b8ac4;
    --orange: #f28a1e;
    --orange-deep: #ef6a22;
    --white: #ffffff;
    --ink: #4a4a4a;
    --rule: #6b6b6b;
  }
  * { box-sizing: border-box; margin: 0; padding: 0; }
  html, body {
    width: 1200px; height: 900px; overflow: hidden;
    background: var(--backdrop);
    font-family: "Source Sans 3", "Myriad Pro", sans-serif;
  }
  .card {
    position: absolute;
    width: 575px; height: 329px;
    border-radius: 23px;
    overflow: hidden;
  }

  /* Front */
  .card-front {
    left: 312px; top: 117px;
    background: linear-gradient(150deg, var(--blue-light) 0%, #2f68a8 40%, var(--navy) 75%);
    color: var(--white);
  }
  .front-glow {
    position: absolute; right: -40px; top: -30px;
    width: 360px; height: 300px; border-radius: 50%;
    background: rgba(255,255,255,0.07);
  }
  .services { position: absolute; left: 29px; top: 31px; }
  .services-title {
    color: var(--orange); font-size: 21px; font-weight: 600; line-height: 26px;
  }
  .service-list { list-style: none; margin-top: 1px; }
  .service-list li {
    font-size: 18px; line-height: 22px; font-weight: 400;
    display: flex; align-items: center; gap: 6px;
  }
  .bullet {
    width: 9px; height: 9px; border: 1.5px solid var(--orange);
    border-radius: 50%; border-right-color: transparent;
  }
  .links { position: absolute; left: 29px; top: 157px; }
  .links li { list-style: none; font-size: 18px; line-height: 25px; display: flex; align-items: center; gap: 7px; }
  .links .square { width: 14px; height: 14px; border-radius: 3px; background: var(--orange); }
  .links .site { color: var(--orange); font-size: 18px; }
  .front-name {
    position: absolute; right: 27px; top: 272px;
    font-size: 44px; font-weight: 700; line-height: 1; letter-spacing: 0.5px;
    color: var(--white);
  }

  /* Back */
  .card-back {
    left: 298px; top: 489px;
    background: var(--white);
  }
  .brand {
    position: absolute; left: 0; width: 287px; top: 138px;
    display: flex; justify-content: center; align-items: center; gap: 8px;
    font-size: 31px; font-weight: 700; color: var(--orange);
  }
  .brand .dot { width: 14px; height: 14px; border-radius: 50%; background: var(--blue-text); }
  .divider {
    position: absolute; left: 287px; top: 49px; width: 1px; height: 216px;
    background: var(--rule);
  }
  .contact { position: absolute; left: 332px; top: 56px; color: var(--ink); }
  .contact-name { font-size: 22px; font-weight: 600; color: var(--blue-text); letter-spacing: 0.6px; line-height: 26px; }
  .contact-title { font-size: 15px; font-weight: 300; line-height: 18px; }
  .contact-address { margin-top: 39px; font-size: 15px; font-weight: 300; line-height: 20px; }
  .contact-lines { margin-top: 10px; font-size: 15px; font-weight: 300; line-height: 20.5px; }
  .contact-lines .label { color: var(--blue-text); font-weight: 400; }
  .base-band { position: absolute; left: 0; bottom: 0; width: 575px; height: 80px; }
</style>
</head>
<body>

<section class="card card-front">
  <div class="front-glow"></div>
  <div class="services">
    <h2 class="services-title">Our Service</h2>
    <ul class="service-list">
      <li><span class="bullet"></span>Web Design</li>
      <li><span class="bullet"></span>Internet Marketing</li>
      <li><span class="bullet"></span>Website Management</li>
    </ul>
  </div>
  <ul class="links">
    <li><span class="square"></span>@trelvanmedia</li>
    <li><span class="square"></span>www.friendloop.example/trelvanmedia</li>
    <li class="site">www.trelvanmedia.example</li>
  </ul>
  <div class="front-name">Trelvan Media</div>
</section>

<section class="card card-back">
  <div class="brand"><span class="dot"></span>Trelvan Media</div>
  <div class="divider"></div>
  <div class="contact">
    <div class="contact-name">Mark Lenner</div>
    <div class="contact-title">President/CEO</div>
    <div class="contact-address">4315 W. Calloway Ave.<br>Ste. 140, Tucson, AZ 85792</div>
    <div class="contact-lines">
      <div><span class="label">Phone.</span> 520-381-7459</div>
      <div><span class="label">Toll Free.</span> 866-381-7459</div>
      <div><span class="label">Email.</span> mark@trelvanmedia.example</div>
    </div>
  </div>
  <svg class="base-band" viewBox="0 0 575 80" aria-hidden="true">
    <path d="M0,58 Q300,62 575,30 L575,80 L0,80 Z" fill="var(--navy)"/>
    <rect x="0" y="50" width="575" height="4" fill="var(--orange-deep)"/>
  </svg>
</section>

</body>
</html>
```